Yoga Workshop - Yoga Practice information flyer

I am a yoga teacher who will be presenting a workshop on yoga for sleep and need a brochure for my clients which outlines a practice that I give them so they can do the practice at home. Ideally I would like a brochure that is a single A3 size of paper in size that folds in half to an A4 booklet with the entire practice on the centre section to make it easy for people to do the practice at home with just one open page in front of them:
* Front page detailing "Yoga for Sleep Workshop" and "Restorative Yoga Practice"
* Centre contains the information on the practice contained in the attached word document. The practice consists of 5 postures, so there needs to be five separate sections which have the pictures of the postures (attached in uploaded files) and the wording contained in the attached word document. All pictures uploaded need to be included in the flyer as each posture has different pictures demonstrating the posture using yoga props or using things people have at home
* Back page containing a picture of myself (picture uploaded in files) with some information about me (contained in the attached word document) and my website www.calmdrift.com.au

I also need this flyer to be able to printed on 2 double sided A4 sheets of paper so will require 2 x pdf file versions. Importantly, for the centre section of the flyer, the design needs to ensure if it is printed on A4 paper, the wording and pictures for each of the postures are not separated over two pages

Target Market(s)

Existing clients

Requirements
Must have
• Detailed in project description
Nice to have
• The word document also contains some quotes. These do not need to be included in the flyer. If there is room and there is room for one or two of those please include where it would look good
Should not have
• Stock pictures of people in yoga postures which a normal everyday person could not get into

```html
<!DOCTYPE html>
<html lang="en">
<head>
<meta charset="utf-8">
<title>Yoga for Sleep Workshop</title>
<link rel="stylesheet" href="https://fonts.googleapis.com/css2?family=Josefin+Sans:wght@300;400;600;700&display=swap">
<style>
  :root {
    --clay: #cd8661;
    --peach: #e6a986;
    --navy: #34485f;
    --paper: #ffffff;
  }
  html, body {
    margin: 0;
    padding: 0;
    overflow: hidden;
    background: var(--paper);
  }
  .flyer {
    position: relative;
    width: 848px;
    height: 1200px;
    overflow: hidden;
    background: var(--navy);
    font-family: "Josefin Sans", sans-serif;
  }
  .backdrop {
    position: absolute;
    inset: 0;
    width: 848px;
    height: 1200px;
  }
  .title {
    position: absolute;
    top: 38px;
    left: 0;
    width: 848px;
    margin: 0;
    text-align: center;
    font-weight: 700;
    font-size: 88px;
    line-height: 98px;
    letter-spacing: 1px;
  }
  .title__lead { display: block; color: var(--clay); }
  .title__main { display: block; color: var(--navy); }

  .pose-figure {
    position: absolute;
    left: 58px;
    top: 458px;
    width: 222px;
    height: 314px;
    background: var(--clay);
    border-radius: 111px 111px 60px 60px;
  }

  .practice {
    position: absolute;
    left: 320px;
    top: 384px;
    width: 480px;
    color: var(--paper);
  }
  .practice__heading {
    margin: 0 0 20px;
    color: var(--peach);
    font-weight: 700;
    font-size: 24.5px;
    letter-spacing: 0.6px;
  }
  .practice p {
    margin: 0 0 24px;
    font-size: 17.5px;
    line-height: 24px;
    font-weight: 400;
    letter-spacing: 0.5px;
  }

  .quote {
    position: absolute;
    margin: 0;
    text-align: right;
    font-weight: 300;
    font-size: 17.5px;
    line-height: 22px;
    letter-spacing: 0.4px;
  }
  .quote--first { right: 86px; top: 925px; color: var(--peach); }
  .quote--second { right: 44px; top: 1004px; color: var(--paper); }
  .quote cite { display: block; font-style: normal; }

  .brand {
    position: absolute;
    left: 0;
    top: 954px;
    width: 462px;
    text-align: center;
  }
  .brand__mark {
    width: 92px;
    height: 92px;
    margin: 0 auto 14px;
    border: 3px solid var(--clay);
    border-radius: 50%;
    box-sizing: border-box;
  }
  .brand__name {
    margin: 0;
    color: var(--navy);
    font-weight: 700;
    font-size: 46px;
    line-height: 50px;
  }
  .brand__tagline {
    position: absolute;
    left: 34px;
    top: 1144px;
    margin: 0;
    color: var(--navy);
    font-size: 15px;
    font-weight: 400;
    letter-spacing: 3.6px;
    white-space: nowrap;
  }
</style>
</head>
<body>
<main class="flyer">
  <svg class="backdrop" viewBox="0 0 848 1200" aria-hidden="true">
    <path d="M0 0 H848 V246 Q424 395 0 246 Z" fill="var(--clay)"/>
    <path d="M0 0 H848 V246 Q424 372 0 246 Z" fill="var(--paper)" transform="translate(0 -1)"/>
    <path d="M0 0 H848 V244 Q424 360 0 244 Z" fill="var(--paper)"/>
    <path d="M0 1060 C120 990 220 905 231 860 C260 950 380 1020 470 1075 C530 1115 555 1160 565 1200 L0 1200 Z" fill="var(--clay)"/>
    <path d="M0 1082 C120 1012 215 925 231 878 C258 965 378 1035 462 1088 C520 1128 545 1165 559 1200 L0 1200 Z" fill="var(--paper)"/>
  </svg>

  <h1 class="title">
    <span class="title__lead">Yoga for Sleep</span>
    <span class="title__main">Workshop</span>
  </h1>

  <div class="pose-figure" role="img" aria-label="Silhouette of a person seated cross-legged in meditation with hands joined above the head"></div>

  <section class="practice">
    <h2 class="practice__heading">Restorative Yoga Sleep Sequence</h2>
    <p>Use this sequence to relax and unwind at the end of a day or before bed. Settle comfortably into each posture for about 5-7 minutes. Set a timer to let you know when it is time to change position, and you can also listen to any music you find relaxing at the same time. The audio recording from the Yoga for Sleep Workshop can also be used to recreate the practice at home.</p>
    <p>The postures in this sequence may be practiced together or individually. In the middle of the night when you can’t sleep or at the end of a day, you might like to experiment with resting in just one of these postures for about 5-10 minutes.</p>
    <p>Use your time in these postures to allow your body to release into the support of the surfaces you are resting on and settle into softness and relaxation.</p>
  </section>

  <blockquote class="quote quote--first">
    “Life isn’t as serious as the mind makes it out to be”
    <cite>—Elias Thornbury</cite>
  </blockquote>
  <blockquote class="quote quote--second">
    “Posture should be steady and comfortable”
    <cite>—Yoga Sutras of Anvara</cite>
  </blockquote>

  <div class="brand">
    <div class="brand__mark"></div>
    <p class="brand__name">Calm Drift</p>
  </div>
  <p class="brand__tagline">Be the change you wish to see in the world</p>
</main>
</body>
</html>
```